Letter design, envelope design, and more

Hello, we the Tavrin Gmbh are looking for our shop. Letter C5. Design does not have to be like a business card, so it can have straight lines. Only the color is important. The logo is the text under TaVRin omit.It should not be playful but Profesionel

Font styles to use
Sans Serif

Colors
0555a3
3176b5
85abd2
85cae6
34a7d8
0792cd
cee9f5
cfdfed
000000

Requirements
Must have
• Color like business card, Please, with the text under TaVRin, Correct address Lindmattstr. 4 Zip code 9517 Seewald, as well as Couvert Without addressing only design and logo with TaVrn
Nice to have
• more writing articles
Should not have
• Not too colored, Text under TaVRin, bright colors

```html
<!DOCTYPE html>
<html lang="en">
<head>
<meta charset="utf-8">
<title>Tavrin Gmbh – Stationery</title>
<link href="https://fonts.googleapis.com/css2?family=Lato:ital,wght@0,400;0,700;0,900;1,700&display=swap" rel="stylesheet">
<style>
  :root {
    --stage: #e1e2e4;
    --paper: #ffffff;
    --paper-shade: #e9e9eb;
    --navy: #23236a;
    --flap: #35346f;
    --edge: #c9c9cd;
    --body-text: #4a4a52;
    --muted: #5a5a62;
  }
  * { margin: 0; padding: 0; box-sizing: border-box; }
  html, body { width: 1200px; height: 641px; overflow: hidden; background: var(--stage); }
  body { position: relative; font-family: "Lato", Arial, sans-serif; }

  .wordmark {
    font-family: "Lato", Arial, sans-serif;
    font-weight: 900;
    color: var(--navy);
    letter-spacing: 0.5px;
    white-space: nowrap;
  }

  /* Letterhead */
  .letterhead {
    position: absolute; left: 74px; top: 64px; width: 364px; height: 512px;
    background: linear-gradient(160deg, var(--paper) 35%, var(--paper-shade) 100%);
    box-shadow: 0 0 0 1px #d2d2d6;
  }
  .letterhead .wordmark {
    position: absolute; top: 20px; left: 0; width: 100%; text-align: center; font-size: 24px;
  }
  .letterhead .salutation {
    position: absolute; left: 20px; top: 85px; font-weight: 700; font-size: 10px; color: var(--navy);
  }
  .letterhead .body-copy { position: absolute; left: 20px; top: 103px; width: 327px; }
  .letterhead .body-copy p {
    font-size: 6.6px; line-height: 10.8px; color: var(--body-text); text-align: justify; margin-bottom: 10.4px;
  }
  .letterhead .closing { position: absolute; left: 20px; top: 396px; font-size: 11.5px; color: var(--muted); }
  .letterhead .signature {
    position: absolute; left: 21px; top: 412px; font-size: 16px; font-weight: 700; font-style: italic; color: var(--navy);
  }
  .letterhead .footer-rule { position: absolute; left: 0; right: 0; top: 490px; height: 1px; background: var(--navy); }
  .letterhead .footer-band {
    position: absolute; left: 0; right: 0; bottom: 0; height: 18px; background: var(--navy);
    display: flex; align-items: center; justify-content: center; gap: 6px;
    color: #fff; font-size: 6.8px;
  }
  .footer-band .sep { width: 1px; height: 9px; background: rgba(255,255,255,0.5); }
  .footer-band .item { display: flex; align-items: center; gap: 3px; }
  .footer-band svg { width: 7px; height: 7px; }

  /* Envelopes */
  .envelope {
    position: absolute; width: 540px; height: 242px; background: var(--paper);
    box-shadow: 0 0 0 1px var(--edge); overflow: hidden;
  }
  .envelope svg.flap { position: absolute; left: 0; top: 0; }
  .envelope-back-dark { left: 594px; top: 76px; }
  .envelope-back-light { left: 554px; top: 179px; }
  .envelope-front { left: 464px; top: 287px; }

  .flap-mark {
    position: absolute; width: 100%; text-align: center; font-size: 22px;
  }
  .envelope-back-dark .flap-mark { top: 30px; color: #fff; }
  .envelope-back-light .flap-mark { top: 34px; }

  .envelope-front .wordmark { position: absolute; left: 17px; top: 18px; font-size: 24px; }
  .envelope-front .sender {
    position: absolute; left: 15px; top: 64px; font-size: 9.6px; color: #222; display: flex; align-items: center; gap: 4px;
  }
  .envelope-front .footer-rule { position: absolute; left: 0; right: 0; top: 216px; height: 1px; background: var(--navy); }
  .envelope-front .footer-band {
    position: absolute; left: 0; right: 0; bottom: 0; height: 23px; background: var(--navy);
    color: #fff; font-size: 9.6px; letter-spacing: 1.8px; text-align: center; line-height: 23px;
  }
  .envelope-front .footer-band b { font-weight: 700; }
</style>
</head>
<body>

  <section class="envelope envelope-back-dark">
    <svg class="flap" width="540" height="242" viewBox="0 0 540 242">
      <path d="M0 0 H540 L534 28 C530 44 520 52 500 56 L290 94 C278 96 262 96 250 94 L40 56 C20 52 10 44 6 28 Z" fill="var(--flap)"/>
    </svg>
    <div class="flap-mark wordmark">TAVRIN</div>
  </section>

  <section class="envelope envelope-back-light">
    <svg class="flap" width="540" height="242" viewBox="0 0 540 242">
      <path d="M0 0 L8 30 C14 46 24 52 44 56 L248 94 C260 96 280 96 292 94 L496 56 C516 52 526 46 532 30 L540 0" fill="none" stroke="#b9b9be" stroke-width="0.8"/>
    </svg>
    <div class="flap-mark wordmark">TAVRIN</div>
  </section>

  <section class="envelope envelope-front">
    <div class="wordmark">TAVRIN GMBH</div>
    <div class="sender">
      <svg width="9" height="9" viewBox="0 0 10 10"><circle cx="5" cy="5" r="4.3" fill="none" stroke="var(--navy)" stroke-width="1"/><circle cx="5" cy="4.3" r="1.4" fill="var(--navy)"/></svg>
      Lindmattstr. 4, Zip code 9517 Seewald
    </div>
    <div class="footer-rule"></div>
    <div class="footer-band">www.<b>tavrin</b>.ch</div>
  </section>

  <article class="letterhead">
    <div class="wordmark">TAVRIN GMBH</div>
    <div class="salutation">Dear Mr. Lorem,</div>
    <div class="body-copy">
      <p>Lorem ipsum dolor sit amet, consectetuer adipiscing elit, sed diam nonummy nibh euismod tincidunt ut laoreet dolore magna aliquam erat volutpat. Ut wisi enim ad minim veniam, quis nostrud exerci tation ullamcorper suscipit lobortis nisl ut aliquip ex ea commodo consequat. Duis autem vel eum iriure dolor in hendiusto odio dignissim qui blandit praesent luptatum zzril delenit.facilisi.</p>
      <p>Lorem ipsum dolor sit amet, consectetuer adipiscing elit, sed diam nonummy nibh euismod tincidunt ut laoreet dolore magna aliquam erat volutpat. Ut wisi enim ad minim veniam, quis nostrud exerci tation ullamcorper suscipit lobortis nisl ut aliquip ex ea commodo consequat.</p>
      <p>Lorem ipsum dolor sit amet, consectetuer adipiscing elit, sed diam nonummy nibh euismod tincidunt ut laoreet dolore magna aliquam erat volutpat. Ut wisi enim ad minim veniam, quis nostrud exerci tation ullamcorper suscipit lobortis nisl ut aliquip ex ea commodo consequat. Duis autem vel eum iriure dolor in hendiusto odio dignissim qui blandit praesent luptatum zzril delenit.facilisi.</p>
      <p>Lorem ipsum dolor sit amet, consectetuer adipiscing elit, sed diam nonummy nibh euismod tincidunt ut laoreet dolore magna aliquam erat volutpat. Ut wisi enim ad minim veniam, quis nostrud exerci tation ullamcorper suscipit lobortis nisl ut aliquip ex ea commodo consequat.</p>
      <p>Lorem ipsum dolor sit amet, consectetuer adipiscing elit, sed diam nonummy nibh euismod tincidunt ut laoreet dolore magna aliquam erat volutpat. Ut wisi enim ad minim veniam, quis nostrud exerci tation ullamcorper suscipit lobortis nisl ut aliquip ex ea commodo consequat. Duis autem vel eum iriure dolor in hendiusto odio dignissim qui blandit praesent luptatum zzril delenit.facilisi.</p>
      <p>Lorem ipsum dolor sit amet, consectetuer adipiscing elit, sed diam nonummy nibh euismod tincidunt ut laoreet dolore magna aliquam erat volutpat. Ut wisi enim ad minim veniam, quis nostrud exerci tation ullamcorper suscipit lobortis nisl ut aliquip ex ea commodo consequat.</p>
    </div>
    <div class="closing">Sincerely Your,</div>
    <div class="signature">Your Name</div>
    <div class="footer-rule"></div>
    <footer class="footer-band">
      <span class="item"><svg viewBox="0 0 10 10"><circle cx="5" cy="5" r="4.2" fill="none" stroke="#fff" stroke-width="1"/><circle cx="5" cy="4.3" r="1.4" fill="#fff"/></svg>Lindmattstr. 4, Zip code 9517 Seewald</span>
      <span class="sep"></span>
      <span class="item"><svg viewBox="0 0 10 10"><path d="M2.5 1.5 L4 1.5 L4.6 3.4 L3.6 4.2 C4.2 5.5 4.9 6.2 6 6.6 L6.8 5.6 L8.6 6.2 L8.6 7.7 C8.6 8.2 8.2 8.6 7.6 8.5 C4.6 8.1 2 5.5 1.6 2.6 C1.5 2 1.9 1.5 2.5 1.5 Z" fill="#fff"/></svg>+41 71 555 02 48</span>
      <span class="sep"></span>
      <span class="item"><svg viewBox="0 0 10 10"><rect x="1" y="2.3" width="8" height="5.6" fill="#fff"/><path d="M1 2.5 L5 5.5 L9 2.5" fill="none" stroke="var(--navy)" stroke-width="0.8"/></svg>info@tavrin.ch</span>
      <span class="sep"></span>
      <span class="item"><svg viewBox="0 0 10 10"><circle cx="5" cy="5" r="4" fill="none" stroke="#fff" stroke-width="0.9"/><ellipse cx="5" cy="5" rx="1.8" ry="4" fill="none" stroke="#fff" stroke-width="0.7"/><path d="M1 5 H9" stroke="#fff" stroke-width="0.7"/></svg>www.tavrin.ch</span>
    </footer>
  </article>

</body>
</html>
```